Healthcare and Professional IT Services Company need a redesigned business card

We are a IT Services company that targets small medical practices and professional business such as Attorneys, Accounts, Architects etc. We want to communicate a professional yet friendly image using recent logo redesign here on ArtHarbor. Like to see the colors blue and orange in the design. Must use the Tall Pine Computing as displayed in the new logo - then also want to incorporate the fish logo as well.

Target Market(s)

Small medical and professional services

Industry/Entity Type

It Company

Contact Information for Business Card

The usual stuff, place for name address phone website. Also maybe our tagline which is "rooted in good support"

Requirements
Must have
• My new logo and the fish somewhere on the card

```html
<!DOCTYPE html>
<html lang="en">
<head>
<meta charset="utf-8">
<title>Tall Pine Computing – Business Card</title>
<link href="https://fonts.googleapis.com/css2?family=Tinos:wght@400&family=PT+Sans:wght@400&display=swap" rel="stylesheet">
<style>
  :root {
    --stage: #e9e6e1;
    --card-white: #f4f5f6;
    --blue-light: #35b2e3;
    --blue-deep: #1e8fcc;
    --brand-blue: #3aa9dc;
    --ink-black: #0b0b0c;
    --text-white: #ffffff;
    --accent-orange: #e9a23b;
  }
  * { box-sizing: border-box; margin: 0; padding: 0; }
  html, body { width: 1200px; height: 892px; overflow: hidden; }
  body {
    background: var(--stage);
    font-family: "Tinos", "Times New Roman", serif;
    display: flex;
    align-items: center;
    justify-content: center;
    gap: 50px;
  }
  .card {
    width: 525px;
    height: 300px;
    border-radius: 18px;
    overflow: hidden;
    position: relative;
    box-shadow: 0 8px 24px rgba(0,0,0,.18);
  }

  /* Front */
  .card--front { background: var(--card-white); }
  .front__logo-panel {
    position: absolute; left: 0; top: 0;
    width: 215px; height: 250px;
    display: flex; flex-direction: column;
    align-items: center; justify-content: center; gap: 14px;
  }
  .brand-mark { width: 16px; height: 16px; border-radius: 50%; background: var(--accent-orange); }
  .brand-name {
    font-family: "Tinos", "Times New Roman", serif;
    font-size: 27px; line-height: 1.1;
    color: var(--brand-blue);
    text-align: center;
  }
  .front__info-panel {
    position: absolute; left: 215px; top: 0; right: 0; height: 250px;
    background: linear-gradient(160deg, var(--blue-deep) 0%, var(--blue-light) 100%);
    color: var(--text-white);
    padding: 62px 0 0 42px;
  }
  .person-name { font-size: 38px; font-weight: 400; margin-bottom: 26px; }
  .contact-list { list-style: none; font-family: "PT Sans", Arial, sans-serif; font-size: 15.5px; }
  .contact-list li { display: flex; align-items: flex-start; gap: 12px; margin-bottom: 7px; line-height: 1.3; }
  .contact-icon {
    flex: none; width: 15px; height: 15px; margin-top: 2px;
    background: var(--text-white); border-radius: 2px;
    display: flex; align-items: center; justify-content: center;
  }
  .front__tagline-band {
    position: absolute; left: 0; right: 0; bottom: 0; height: 50px;
    background: var(--ink-black);
    display: flex; align-items: center; justify-content: center;
    color: var(--brand-blue); font-size: 21px;
    white-space: nowrap;
  }

  /* Back */
  .card--back {
    background: var(--ink-black);
    display: flex; flex-direction: column;
    align-items: center; justify-content: center; gap: 18px;
  }
  .card--back .brand-name { font-size: 40px; }
  .card--back .brand-mark { width: 22px; height: 22px; }
</style>
</head>
<body>
  <section class="card card--front" aria-label="Business card front">
    <div class="front__logo-panel">
      <span class="brand-mark"></span>
      <span class="brand-name">Tall Pine<br>Computing</span>
    </div>
    <div class="front__info-panel">
      <h1 class="person-name">Daniel Reyes</h1>
      <ul class="contact-list">
        <li>
          <span class="contact-icon"><svg width="10" height="10" viewBox="0 0 10 10"><path d="M2 1 L4 1 L4.5 3 L3.5 4 Q4.5 6 6 6.5 L7 5.5 L9 6 L9 8 Q5 9 2 6 Q0.5 3.5 2 1Z" fill="#1e8fcc"/></svg></span>
          <span>480-555-0142</span>
        </li>
        <li>
          <span class="contact-icon"><svg width="10" height="10" viewBox="0 0 10 10"><circle cx="5" cy="5" r="4" fill="none" stroke="#1e8fcc" stroke-width="1.2"/><path d="M1 5 H9 M5 1 Q2.5 5 5 9 M5 1 Q7.5 5 5 9" fill="none" stroke="#1e8fcc" stroke-width="0.9"/></svg></span>
          <span>www.tallpinecomputing.com</span>
        </li>
        <li>
          <span class="contact-icon"><svg width="10" height="10" viewBox="0 0 10 10"><path d="M1 5 L5 1.5 L9 5 H7.8 V9 H2.2 V5Z" fill="#1e8fcc"/></svg></span>
          <span>2710 N.Cedar Ridge Road Tempe,<br>Arizona 85281</span>
        </li>
      </ul>
    </div>
    <div class="front__tagline-band">
      <p class="tagline">Also maybe our tagline which is "rooted in good support"</p>
    </div>
  </section>

  <section class="card card--back" aria-label="Business card back">
    <span class="brand-mark"></span>
    <span class="brand-name">Tall Pine Computing</span>
  </section>
</body>
</html>
```